Banner Ad Design Project

I require banner ad designs with the below wording.

1. Join Today and Make Money Tomorrow. Unlimited Income. Click Here Now

2. I lost my job. Now I Make Over $5,000 Per Week From Home. You Can Too. Free Info, Apply Now

I require sizes: 300x250 and 728x90 and 468x60 and 120x240

The design should communicate legitimate, accredited, online business.

Industry/Entity Type

Business

Requirements
Should not have
• Creative attributes to avoid*
Phone numbers in creative
Creative with no click buttons
Interactive creative
Brand messaging with no call to action
Creative with long looping times

```html
<!DOCTYPE html>
<html lang="en">
<head>
<meta charset="utf-8">
<title>Banner Ad Set – Join Today / Work From Home</title>
<link rel="stylesheet" href="https://fonts.googleapis.com/css2?family=Roboto+Condensed:wght@400;700&family=Tinos:ital@1&display=swap">
<style>
  :root {
    --stage-light: #d6d6d6;
    --stage-dark: #8c8c8c;
    --ink-black: #0d0d0d;
    --ink-charcoal: #3a3a3a;
    --pink: #c9134f;
    --pink-deep: #a80c3f;
    --pink-light: #de2a66;
    --gold-top: #fff37c;
    --gold-bottom: #e9b100;
    --white: #ffffff;
    --photo-warm: #d9c3b4;
    --photo-cool: #e6e3e1;
    --cash-green: #7dbb5a;
    --cash-gold: #d9c24a;
    --btn-text: #1a1a1a;
  }
  * { box-sizing: border-box; margin: 0; padding: 0; }
  html, body { width: 1200px; height: 900px; overflow: hidden; }
  body {
    background: radial-gradient(ellipse at 50% 45%, var(--stage-light) 0%, #b4b4b4 55%, var(--stage-dark) 100%);
    font-family: "Roboto Condensed", "Arial Narrow", sans-serif;
    position: relative;
  }
  .banner { position: absolute; overflow: hidden; }
  .banner-bg { position: absolute; inset: 0; width: 100%; height: 100%; }
  .txt { position: absolute; white-space: nowrap; line-height: 1; }
  .gold {
    background: linear-gradient(180deg, var(--gold-top) 0%, var(--gold-bottom) 100%);
    -webkit-background-clip: text; background-clip: text; color: transparent;
    font-weight: 700;
  }
  .white { color: var(--white); }
  .script { font-family: "Tinos", "Times New Roman", serif; font-style: italic; color: var(--white); }
  .center { transform: translateX(-50%); text-align: center; }
  .btn {
    position: absolute; background: linear-gradient(180deg, #ffffff 0%, #e4e4e4 100%);
    color: var(--btn-text); display: flex; align-items: center; justify-content: center;
    box-shadow: 0 2px 4px rgba(0,0,0,.35);
  }

  /* 300x250 – Join Today */
  .rect-join { left: 141px; top: 88px; width: 449px; height: 374px; }
  /* 300x250 – Lost my job */
  .rect-story { left: 621px; top: 88px; width: 450px; height: 374px; }
  /* 728x90 – Join Today */
  .leader-join { left: 57px; top: 507px; width: 1092px; height: 134px; }
  /* 728x90 – Lost my job */
  .leader-story { left: 57px; top: 673px; width: 1092px; height: 134px; }
</style>
</head>
<body>

<!-- Medium rectangle: Join Today -->
<section class="banner rect-join">
  <svg class="banner-bg" viewBox="0 0 449 374" preserveAspectRatio="none">
    <defs>
      <linearGradient id="darkA" x1="0" y1="0" x2="0" y2="1">
        <stop offset="0" stop-color="#4a4a4a"/><stop offset="1" stop-color="#050505"/>
      </linearGradient>
      <linearGradient id="pinkA" x1="0" y1="0" x2="0" y2="1">
        <stop offset="0" stop-color="#de2a66"/><stop offset="1" stop-color="#a80c3f"/>
      </linearGradient>
    </defs>
    <rect width="449" height="374" fill="url(#darkA)"/>
    <path d="M0 330 Q220 300 449 235 V374 H0 Z" fill="url(#pinkA)"/>
    <path d="M0 322 Q220 292 449 227 V235 Q220 300 0 330 Z" fill="#ffffff"/>
  </svg>
  <div role="img" aria-label="Photo of a smiling businesswoman in glasses" style="position:absolute;left:0;top:0;width:188px;height:374px;background:linear-gradient(90deg,var(--photo-cool),var(--photo-warm) 60%,#2a2a2a);"></div>
  <div role="img" aria-label="Stack of banknotes" style="position:absolute;left:294px;top:204px;width:112px;height:90px;border-radius:4px;background:linear-gradient(135deg,var(--cash-gold),var(--cash-green));"></div>
  <div class="txt gold" style="left:159px;top:26px;font-size:55px;">Join Today</div>
  <div class="txt white" style="left:173px;top:96px;font-size:24px;">&amp; Make Money&nbsp; Tomorrow</div>
  <div class="txt script" style="left:167px;top:148px;font-size:34px;">Unlimited Income</div>
  <div class="btn" style="left:253px;top:305px;width:196px;height:57px;border-radius:29px 0 0 29px;font-size:24px;">Click Here Now</div>
</section>

<!-- Medium rectangle: Lost my job -->
<section class="banner rect-story">
  <svg class="banner-bg" viewBox="0 0 450 374" preserveAspectRatio="none">
    <defs>
      <linearGradient id="pinkB" x1="0" y1="0" x2="0" y2="1">
        <stop offset="0" stop-color="#de2a66"/><stop offset="1" stop-color="#b30d44"/>
      </linearGradient>
    </defs>
    <rect width="450" height="374" fill="url(#pinkB)"/>
    <path d="M0 334 Q225 290 450 318 V374 H0 Z" fill="#ffffff"/>
  </svg>
  <div role="img" aria-label="Photo of an excited businesswoman cheering with raised arms" style="position:absolute;left:0;top:0;width:450px;height:152px;background:linear-gradient(90deg,var(--photo-cool),var(--photo-warm) 55%,var(--photo-cool));clip-path:path('M0 0 H450 V152 Q250 70 0 70 Z');"></div>
  <div class="txt white center" style="left:225px;top:174px;font-size:28px;">I lost my job. Now I Make Over</div>
  <div class="txt gold center" style="left:225px;top:210px;font-size:42px;">$5,000 Per Week</div>
  <div class="txt white center" style="left:225px;top:263px;font-size:28px;">From Home</div>
  <div class="txt center" style="left:225px;top:328px;font-size:27px;color:var(--pink);">You Can Too. Free Info, Apply Now</div>
</section>

<!-- Leaderboard: Join Today -->
<section class="banner leader-join">
  <svg class="banner-bg" viewBox="0 0 1092 134" preserveAspectRatio="none">
    <defs>
      <linearGradient id="darkC" x1="0" y1="0" x2="0" y2="1">
        <stop offset="0" stop-color="#4a4a4a"/><stop offset="1" stop-color="#050505"/>
      </linearGradient>
      <linearGradient id="pinkC" x1="0" y1="0" x2="0" y2="1">
        <stop offset="0" stop-color="#de2a66"/><stop offset="1" stop-color="#a80c3f"/>
      </linearGradient>
    </defs>
    <rect width="1092" height="134" fill="url(#pinkC)"/>
    <path d="M0 0 H640 Q600 70 610 134 H0 Z" fill="url(#darkC)"/>
  </svg>
  <div role="img" aria-label="Photo of a smiling businesswoman in glasses" style="position:absolute;left:0;top:0;width:90px;height:134px;background:linear-gradient(90deg,var(--photo-cool),var(--photo-warm));"></div>
  <div role="img" aria-label="Stacks of banknotes" style="position:absolute;left:445px;top:0;width:218px;height:134px;background:linear-gradient(135deg,var(--cash-gold),var(--cash-green) 60%,#4f8f3a);"></div>
  <div class="txt gold" style="left:105px;top:18px;font-size:68px;">Join Today</div>
  <div class="txt white" style="left:115px;top:92px;font-size:27px;">&amp; Make Money&nbsp; Tomorrow</div>
  <div class="txt script" style="left:673px;top:27px;font-size:40px;">Unlimited</div>
  <div class="txt script" style="left:688px;top:78px;font-size:40px;">Income</div>
  <div class="btn" style="left:880px;top:26px;width:212px;height:85px;border-radius:43px 0 0 43px;font-size:30px;">Click Here Now</div>
</section>

<!-- Leaderboard: Lost my job -->
<section class="banner leader-story">
  <svg class="banner-bg" viewBox="0 0 1092 134" preserveAspectRatio="none">
    <defs>
      <linearGradient id="pinkD" x1="0" y1="0" x2="0" y2="1">
        <stop offset="0" stop-color="#de2a66"/><stop offset="1" stop-color="#b30d44"/>
      </linearGradient>
    </defs>
    <rect width="1092" height="134" fill="#ffffff"/>
    <path d="M0 0 H663 L690 67 L663 134 H0 Z" fill="url(#pinkD)"/>
    <path d="M1092 0 V134 H1055 L1040 67 L1055 0 Z" fill="url(#pinkD)"/>
  </svg>
  <div role="img" aria-label="Photo of an excited businesswoman cheering with raised arms" style="position:absolute;left:0;top:0;width:240px;height:134px;background:linear-gradient(90deg,var(--photo-cool),var(--photo-warm) 60%,var(--photo-cool));clip-path:path('M0 0 H220 Q260 67 225 134 H0 Z');"></div>
  <div class="txt white center" style="left:448px;top:16px;font-size:25px;">I lost my job Now I Make Over</div>
  <div class="txt gold center" style="left:448px;top:50px;font-size:40px;">$5,000 Per Week</div>
  <div class="txt white center" style="left:448px;top:101px;font-size:25px;">From Home</div>
  <div class="txt center" style="left:861px;top:26px;font-size:34px;color:var(--pink);">You Can Too</div>
  <div class="txt center" style="left:861px;top:74px;font-size:34px;color:var(--pink);">Free Info, Apply Now</div>
</section>

</body>
</html>
```